Podiatry clinic requires a modern revamp and editing of existing website.

I would like a fresh new look and updated information for my current business website. An easy to navigate site with prominent address and phone number for call to action. We are a podiatry clinic that focuses on general and sports podiatry.
I would like 4 pages; including Home page, About Us, Services & Contact.
www.brambleridgepodiatry.net

Target Market(s)

Active working professionals.

Industry/Entity Type

Medical

Coding

Coded - Design and coding required

Number of Pages Required

4 page

Font styles to use
Sans Serif

Colors
6b449b

Requirements
Must have
• A modern look with logo and active images; clean and uncluttered. Visible phone number and address for call to action.
• 4 pages - Home, About Us, Services, Contact.
• Home page - update address & service logos.
• About Us - update of personal information.
• Services - Revamp of existing page.
• Contact page to include Google map, email & phone number.
Nice to have
• Ability to add content easily; eg. a blog or adding video onto Home page.
• Link to Facebook page.

```html
<!DOCTYPE html>
<html lang="en">
<head>
<meta charset="utf-8">
<title>Bramble Ridge Podiatry</title>
<link href="https://fonts.googleapis.com/css2?family=Open+Sans:wght@400;600&family=Roboto+Condensed:wght@400&family=Raleway:wght@400;500&family=Lato:wght@400;700&display=swap" rel="stylesheet">
<style>
:root{
  --yellow:#fbc900;
  --purple:#4a3594;
  --lavender:#9c86c1;
  --lilac-card:rgba(98,72,170,.85);
  --grey-band:#5f5f5f;
  --dark:#222;
  --text:#333;
  --orange:#f26a1b;
  --red-btn:#f23a0c;
  --green:#8dc21f;
  --date-yellow:#f5c400;
  --date-red:#e8000c;
  --footer-bottom:#595959;
}
*{box-sizing:border-box;margin:0;padding:0}
html,body{width:1200px;height:2486px;overflow:hidden}
body{position:relative;font-family:"Open Sans",Arial,sans-serif;color:var(--text);background:#fff}
.abs{position:absolute}

/* hero */
.hero{left:0;top:0;width:1200px;height:510px;overflow:hidden}
.hero-photo{left:0;top:0;width:1200px;height:510px;background:linear-gradient(100deg,#6d6577 0%,#8a7f8c 30%,#b3a8ae 55%,#d8d1cf 75%)}
.hero-wedge{left:0;top:0}
.topbar{left:0;top:0;width:1200px;height:33px}
.social-top{right:20px;top:9px;display:flex;gap:28px}
.social-top span{width:14px;height:14px;border-radius:50%;background:#fff;opacity:.9}
.header-bar{left:0;top:33px;width:1200px;height:83px;background:rgba(251,201,0,.82)}
.logo-box{left:129px;top:33px;width:136px;height:80px;background:var(--lavender);display:flex;align-items:center;gap:6px;padding:0 8px}
.logo-box i{width:10px;height:10px;background:var(--purple);flex:none}
.logo-box b{font-family:"Lato",sans-serif;font-weight:700;font-size:15px;line-height:17px;color:#fff}
.nav{left:547px;top:33px;height:83px;display:flex;align-items:center;font-size:13px}
.nav a{color:#4a3594;text-decoration:none;margin-right:28px}
.nav a.active{background:var(--purple);color:#fff;height:83px;line-height:83px;padding:0 12px}
.nav-divider{left:865px;top:52px;width:1px;height:46px;background:rgba(0,0,0,.25)}
.call-top{left:900px;top:55px;display:flex;align-items:center;gap:10px}
.call-top small{display:block;font-size:14px;color:var(--orange);line-height:16px}
.call-top strong{display:block;font-size:19px;font-weight:600;color:#222;line-height:22px}
.arrow-btn{top:245px;width:50px;height:50px;background:rgba(200,200,200,.7)}
.arrow-btn svg{display:block}
.hero-caption{right:134px;top:381px;text-align:right;font-family:"Roboto Condensed",sans-serif;font-size:21px;line-height:33px;color:#111}

/* services */
.service-card{top:534px;width:290px;height:291px}
.service-card h3{height:43px;background:var(--yellow);color:#4a3594;font-family:"Open Sans",sans-serif;font-weight:600;font-size:19px;text-align:center;line-height:43px}
.service-photo{height:248px;background:linear-gradient(160deg,#c4c8d6,#8c8a9b)}
.service-card p{position:absolute;left:0;bottom:0;width:100%;height:83px;background:var(--lilac-card);color:#fff;font-size:12.5px;line-height:24px;text-align:center;padding:6px 14px}

/* welcome */
.welcome{left:0;top:858px;width:1200px;height:312px;background:#fff;overflow:hidden}
.section-rule{display:flex;align-items:center;justify-content:center;gap:6px}
.section-rule i{width:8px;height:5px;display:block}
.section-rule .y{background:var(--yellow)}
.section-rule .p{background:var(--purple)}
.section-rule .line{width:440px;height:3px;background:var(--yellow);margin:0 6px}
.welcome h2{position:absolute;left:0;top:38px;width:1200px;text-align:center;font-weight:400;font-size:26px;color:#222}
.welcome .section-rule{position:absolute;left:0;top:81px;width:1200px}
.welcome-text{position:absolute;left:145px;top:114px;width:910px;text-align:center;font-size:14.5px;line-height:27px;color:#333}
.welcome-cta{position:absolute;left:0;top:234px;width:1200px;text-align:center;font-weight:600;font-size:14.5px;line-height:25px;color:#222}

/* accreditations */
.accred{left:0;top:1170px;width:1200px;height:305px;background:var(--grey-band);overflow:hidden}
.accred h2{position:absolute;left:0;top:20px;width:1200px;text-align:center;color:#fff;font-weight:400;font-size:32px}
.accred .section-rule{position:absolute;left:0;top:79px;width:1200px}
.badge{top:132px;width:204px;height:77px;background:#fff;display:flex;align-items:center;justify-content:center}
.badge i{display:block;width:150px;height:34px;border-radius:4px;background:#dfe3ea}

/* blog + video */
.media{left:0;top:1475px;width:1200px;height:493px;overflow:hidden;background:linear-gradient(120deg,#dedde3 0%,#c9c9d0 35%,#d9d3e6 70%,#c6b7d6 100%)}
.media h2{position:absolute;top:64px;font-weight:400;font-size:31px;color:#222}
.media-rule{position:absolute;top:129px;display:flex;align-items:center;gap:5px}
.media-rule i{display:block;width:8px;height:5px}
.media-rule .line{height:3px;background:var(--yellow)}
.post{left:124px;width:420px;height:70px}
.post-date{position:absolute;left:0;top:0;width:66px;height:66px;color:#fff;text-align:center}
.post-date b{display:block;font-weight:400;font-size:36px;line-height:44px}
.post-date span{display:block;font-size:16px;line-height:18px}
.post h4{position:absolute;left:95px;top:-2px;font-weight:400;font-size:17px;color:#333}
.post hr{position:absolute;left:95px;top:24px;width:310px;border:0;border-top:1px solid #999}
.post p{position:absolute;left:95px;top:28px;width:310px;font-size:11px;line-height:18px;color:#333}
.post p em{display:inline-block;width:11px;height:11px;background:var(--orange);vertical-align:middle;margin-left:10px}
.video-frame{left:693px;top:160px;width:376px;height:265px;background:var(--yellow);padding:17px}
.video-still{width:342px;height:231px;background:linear-gradient(135deg,#e9e9ec,#b9bcc4);position:relative}
.video-controls{position:absolute;left:0;bottom:0;width:100%;height:24px;background:#222}

/* cta */
.cta{left:0;top:1968px;width:1200px;height:222px;background:#fff;overflow:hidden}
.cta-lead{position:absolute;left:128px;top:59px;font-family:"Raleway",sans-serif;font-size:22px;line-height:30px;color:#555}
.cta-note{position:absolute;left:128px;top:137px;font-family:"Raleway",sans-serif;font-size:20px;color:var(--purple)}
.cta-note span{color:var(--red-btn)}
.cta-button{position:absolute;left:765px;top:63px;width:218px;height:62px;background:var(--red-btn);border-radius:3px;color:#fff;text-align:center;font-family:"Raleway",sans-serif}
.cta-button small{display:block;font-size:15px;padding-top:6px;line-height:18px}
.cta-button strong{display:block;font-weight:500;font-size:25px;line-height:30px}

/* footer */
.footer{left:0;top:2190px;width:1200px;height:251px;background:var(--lavender);font-family:"Lato",sans-serif;color:#fff}
.footer h5{position:absolute;top:21px;font-weight:400;font-size:18px;color:#3d2b66}
.quick-links{position:absolute;left:136px;top:72px;list-style:none;font-size:13px;line-height:25px}
.quick-links li::before{content:"›";margin-right:10px;opacity:.8}
.footer-sep{position:absolute;top:60px;width:1px;height:165px;background:rgba(255,255,255,.35)}
.contact-row{position:absolute;left:362px;display:flex;gap:14px;font-size:13.5px;line-height:20px}
.contact-row svg{flex:none;margin-top:2px}
.contact-line{position:absolute;left:385px;width:245px;height:1px;background:rgba(255,255,255,.35)}
.hours{position:absolute;left:652px;top:70px;font-size:13px;line-height:19px}
.hours p{margin-bottom:16px}
.hours-line{position:absolute;left:652px;width:205px;height:1px;background:rgba(255,255,255,.35)}
.footer-logo{position:absolute;left:905px;top:82px;display:flex;align-items:center;gap:8px}
.footer-logo i{display:block;width:14px;height:14px;background:var(--purple)}
.footer-logo b{font-weight:700;font-size:22px;line-height:26px;color:#fff}
.footer-bottom{left:0;top:2441px;width:1200px;height:45px;background:var(--footer-bottom);font-family:"Lato",sans-serif}
.footer-bottom p{position:absolute;left:133px;top:14px;font-size:13px;color:#fff}
.footer-social{position:absolute;left:928px;top:6px;display:flex;gap:8px}
.footer-social span{width:33px;height:33px;border-radius:50%;background:#d9d9d9}
</style>
</head>
<body>

<!-- hero -->
<section class="abs hero">
  <div class="abs hero-photo" role="img" aria-label="Photo of a runner sprinting on a track beside a podiatrist examining an ankle"></div>
  <svg class="abs hero-wedge" width="1200" height="510" viewBox="0 0 1200 510">
    <polygon points="1200,0 1200,510 610,510" fill="#fbc900"/>
  </svg>
  <div class="abs topbar">
    <div class="abs social-top"><span></span><span></span><span></span><span></span></div>
  </div>
  <div class="abs header-bar"></div>
  <div class="abs logo-box"><i></i><b>Bramble Ridge Podiatry</b></div>
  <nav class="abs nav">
    <a class="active" href="#">Home</a>
    <a href="#">About Us</a>
    <a href="#">Services</a>
    <a href="#">Contact</a>
  </nav>
  <div class="abs nav-divider"></div>
  <div class="abs call-top">
    <svg width="28" height="28" viewBox="0 0 28 28"><circle cx="14" cy="14" r="12.5" fill="none" stroke="#222" stroke-width="1.5"/><path d="M10 8c-1.5 1-2 3-1 5.5 1.2 3 3.5 5.4 6.5 6.6 2 .7 3.6.3 4.5-1l-2.3-2.3-2 1c-1.6-.8-3-2.2-3.8-3.8l1-2z" fill="#222"/></svg>
    <div><small>Call Us Today</small><strong>1300 482 207</strong></div>
  </div>
  <div class="abs arrow-btn" style="left:0"><svg width="50" height="50" viewBox="0 0 50 50"><path d="M27 17l-8 8 8 8M35 17l-8 8 8 8" fill="none" stroke="#fff" stroke-width="2"/></svg></div>
  <div class="abs arrow-btn" style="right:0"><svg width="50" height="50" viewBox="0 0 50 50"><path d="M15 17l8 8-8 8M23 17l8 8-8 8" fill="none" stroke="#fff" stroke-width="2"/></svg></div>
  <p class="abs hero-caption">Bramble Ridge Podiatry Is A<br>Podiatry Clinic In The Heart Of<br>Melbourne CBD</p>
</section>

<!-- services -->
<article class="abs service-card" style="left:126px">
  <h3>Sports Injuries</h3>
  <div class="service-photo" role="img" aria-label="Photo of hands supporting an injured ankle"></div>
  <p>Lorem ipsum dolor sit amet, consectetuer adipiscing elit, sed diam nonummy nibh euismod tincidunt ut laoreet.</p>
</article>
<article class="abs service-card" style="left:451px">
  <h3>Orthotic Therapy</h3>
  <div class="service-photo" role="img" aria-label="Photo of an orthotic insole fitted to a foot"></div>
  <p>Lorem ipsum dolor sit amet, consectetuer adipiscing elit, sed diam nonummy nibh euismod tincidunt ut laoreet.</p>
</article>
<article class="abs service-card" style="left:779px">
  <h3>Nail Surgery</h3>
  <div class="service-photo" role="img" aria-label="Photo of a gloved podiatrist treating a toenail"></div>
  <p>Lorem ipsum dolor sit amet, consectetuer adipiscing elit, sed diam nonummy nibh euismod tincidunt ut laoreet.</p>
</article>

<!-- welcome -->
<section class="abs welcome">
  <svg class="abs" style="left:0;top:0" width="1200" height="312" viewBox="0 0 1200 312">
    <defs><linearGradient id="shade" x1="0" y1="0" x2="0" y2="1"><stop offset="0" stop-color="#cfcfcf"/><stop offset="1" stop-color="#fff" stop-opacity="0"/></linearGradient></defs>
    <polygon points="0,0 282,0 0,210" fill="#fbc900"/>
    <polygon points="700,0 1200,0 1200,90" fill="url(#shade)"/>
  </svg>
  <h2>Welcome to Bramble Ridge Podiatry</h2>
  <div class="section-rule"><i class="y"></i><i class="p"></i><span class="line"></span><i class="p"></i><i class="y"></i></div>
  <p class="welcome-text">Bramble Ridge Podiatry is a Podiatry clinic in the heart of Melbourne CBD. We are located between Harlow &amp; Pelham Streets in the Meridian Business Centre / Linden Hotel Complex. Our podiatrists are fully qualified health professionals who are able to diagnose, treat, manage or help to prevent all medical conditions that affect the feet and lower limb.We provide General Podiatry Treatment and some Specialised Services in relation to various foot conditions, including Sports Injuries, Orthotic Therapy and Nail Surgery.</p>
  <p class="welcome-cta">For Appointments or Enquiries please<br>call us on 1300 482 207 &nbsp;or email: &nbsp; info@brambleridgepodiatry.net</p>
</section>

<!-- accreditations -->
<section class="abs accred">
  <svg class="abs" style="left:0;top:0" width="1200" height="305" viewBox="0 0 1200 305">
    <polygon points="936,305 1200,114 1200,305" fill="#4a3594"/>
  </svg>
  <h2>Our Accreditations</h2>
  <div class="section-rule"><i class="y"></i><i class="p"></i><span class="line"></span><i class="p"></i><i class="y"></i></div>
  <div class="abs badge" style="left:176px"><i></i></div>
  <div class="abs badge" style="left:399px"><i></i></div>
  <div class="abs badge" style="left:626px"><i></i></div>
  <div class="abs badge" style="left:850px"><i></i></div>
</section>

<!-- blog and video -->
<section class="abs media" role="img" aria-label="Soft blurred background photo of a laptop on a desk">
  <svg class="abs" style="left:0;top:0" width="1200" height="493" viewBox="0 0 1200 493">
    <polygon points="0,0 215,0 0,198" fill="#fbc900"/>
  </svg>
  <h2 style="left:124px">Latest Blog</h2>
  <div class="media-rule" style="left:131px"><i style="background:#fbc900"></i><i style="background:#4a3594"></i><span class="line" style="width:415px"></span></div>
  <h2 style="left:689px">Our Video</h2>
  <div class="media-rule" style="left:683px"><i style="background:#fbc900"></i><i style="background:#4a3594"></i><span class="line" style="width:375px"></span></div>

  <div class="abs post" style="top:157px">
    <div class="post-date" style="background:var(--green)"><b>03</b><span>Aug</span></div>
    <h4>Lorem ipsum dolor</h4><hr>
    <p>Lorem ipsum dolor sit amet, consectetuer adipiscing elit, sed diam nonummy nibh euismod<em></em></p>
  </div>
  <div class="abs post" style="top:260px">
    <div class="post-date" style="background:var(--date-yellow)"><b>01</b><span>Aug</span></div>
    <h4>Lorem ipsum dolor</h4><hr>
    <p>Lorem ipsum dolor sit amet, consectetuer adipiscing elit, sed diam nonummy nibh euismod<em></em></p>
  </div>
  <div class="abs post" style="top:364px">
    <div class="post-date" style="background:var(--date-red)"><b>01</b><span>Aug</span></div>
    <h4>Lorem ipsum dolor</h4><hr>
    <p>Lorem ipsum dolor sit amet, consectetuer adipiscing elit, sed diam nonummy nibh euismod<em></em></p>
  </div>

  <div class="abs video-frame">
    <div class="video-still" role="img" aria-label="Video still of a patient greeting clinic staff">
      <svg class="abs" style="left:154px;top:86px" width="34" height="26" viewBox="0 0 34 26"><rect width="34" height="26" rx="4" fill="#111"/><polygon points="13,7 23,13 13,19" fill="#fff"/></svg>
      <div class="video-controls">
        <svg width="342" height="24" viewBox="0 0 342 24"><polygon points="10,7 17,12 10,17" fill="#fff"/><rect x="28" y="9" width="6" height="6" fill="#fff"/><rect x="62" y="10" width="160" height="4" rx="2" fill="#555"/><rect x="62" y="10" width="80" height="4" rx="2" fill="#e02020"/><path d="M318 8h6v6M326 16h-6v-6" fill="none" stroke="#fff" stroke-width="1.5"/></svg>
      </div>
    </div>
  </div>
</section>

<!-- call to action -->
<section class="abs cta">
  <svg class="abs" style="left:0;top:0" width="1200" height="222" viewBox="0 0 1200 222">
    <polygon points="903,222 1200,4 1200,222" fill="#4a3594"/>
  </svg>
  <p class="cta-lead">We are eligible service providers for all<br>VetCare Gold Card holders</p>
  <p class="cta-note">RoadCover &amp; SafeWork Plus accepted. &nbsp;<span>On the spot Health insurance</span></p>
  <div class="cta-button"><small>Call Us Today</small><strong>1300 482 207</strong></div>
</section>

<!-- footer -->
<footer class="abs footer">
  <h5 style="left:136px">Quick Links</h5>
  <ul class="quick-links">
    <li>Consulting</li><li>Inspections</li><li>Training</li><li>General Contracing</li><li>Clients</li><li>Contact Us</li>
  </ul>
  <div class="footer-sep" style="left:315px"></div>
  <h5 style="left:358px">Contact Details</h5>
  <div class="contact-row" style="top:68px">
    <svg width="10" height="14" viewBox="0 0 10 14"><path d="M5 0a5 5 0 0 0-5 5c0 4 5 9 5 9s5-5 5-9a5 5 0 0 0-5-5z" fill="#3d2b66"/><circle cx="5" cy="5" r="2" fill="#9c86c1"/></svg>
    <span>Suite 214 / 96 Harlow<br>Street &nbsp;Melbourne &nbsp;3000</span>
  </div>
  <div class="contact-line" style="top:122px"></div>
  <div class="contact-row" style="top:135px">
    <svg width="13" height="13" viewBox="0 0 13 13"><path d="M2.5 0c-1.5 1-2.5 3-1.2 6 1.4 3 3.7 5.3 6.7 6.7 2.5 1 4 .3 5-1.2l-2.5-2.5-2 1.2c-1.5-.8-2.8-2.2-3.6-3.7l1.2-2z" fill="#3d2b66"/></svg>
    <span>1300 482 207</span>
  </div>
  <div class="contact-line" style="top:172px"></div>
  <div class="contact-row" style="top:187px">
    <svg width="14" height="11" viewBox="0 0 14 11"><rect width="14" height="11" fill="#3d2b66"/><path d="M0 0l7 6 7-6" fill="none" stroke="#9c86c1" stroke-width="1.2"/></svg>
    <span>info@brambleridgepodiatry.net</span>
  </div>
  <div class="footer-sep" style="left:651px"></div>
  <h5 style="left:694px">Hours of Operation</h5>
  <div class="hours" style="left:694px">
    <p>Monday to Friday<br>10:00am to 07:00pm</p>
    <p>Saturday<br>10:00am to 05:00pm</p>
    <p>Sunday<br>By Appointment Only</p>
  </div>
  <div class="hours-line" style="left:694px;top:117px"></div>
  <div class="hours-line" style="left:694px;top:170px"></div>
  <div class="footer-logo"><i></i><b>Bramble Ridge<br>Podiatry</b></div>
</footer>
<div class="abs footer-bottom">
  <p>Copyright © 2016 Fernway Digital Studio. &nbsp;All Right Reserved.</p>
  <div class="footer-social"><span></span><span></span><span></span></div>
</div>

</body>
</html>
```